Digital Imaging Website Design Project

This project is for 3 page designs - The main Home page design, department page design & content page design which will utilize most of the home page components.

Client Background - http://www.klmvxco.example

An almost Forty year old established printing company that has a large client base of architect/engineering, as the print shop opened up as a blueprinting company, and over the years has grown, changed and expanded to offer document and digital file management for this industry. KLMVxco. has also always offered color printing services, but recently has expanded their color department to be able to offer amazing dimensional printing, and extreme cutting technology.

These new products and services will be targeted to new industries for repeatable printing needs, promotional, point of purchase color printing, as well as in-store, interior decor/wall. These new printing services are only offered by KLMVXCO in their area, and they want to convey that they are on the leading edge of color printing technology, while at the same time, not eliminating their existing primary business scaring away their traditional client base of architectural/engineering firms that use them for large format printing, scanning and document management services.

1 - Home Page Design
Primary Goals of the design:

1.Provide a new, eye catching engaging website that conveys the above expansion/growth/cutting edge company.
2.Full screen design please to move away from the 'center' bordered up website they currently have.
3.Design Components – We don't have any media to provide you with exception of our logo. We're looking for fresh design that is exciting and engaging imagery. Additionally, we are working on a color/effected version of our logo to place on the color division page, and this will probably tie in with the design you create for us.
4.It should be designed to be able to work as a responsive design as well so that when installed, will work across devices etc..
5.Colors – Same color scheme, but if you have an accent color you'd like to use to make the site pop, go for it!

Requirements:
1.The 4 divisions of the company should be the main feature so that the client depending on which department they are needing, will see those 4 choices clearly in the design, and they'll know to click on one of them to get more information and to their needed services.

2.The main goal of the site is to get visitors to place an order, there should be a feature on the home page for this call to action.

3.Put in an element that communicates the main benefit of KLMVxco. - an area for a 1-line Statement/Call to Action / Overall Company Benefit/

4.The 4 divisions need to have eye catching elements related to their products and services, and that clearly illustrate that the user should click on that to go to the appropriate area for products and services

Reprographics
This department is specifically geared to architect/engineering industry
BYLine for optional Use: Partnering with Building Industry Providers since 1975
Related pages for better understanding:
http://www.klmvxco.example/services/portland_professional_printing_services
http://www.klmvxco.example/services/reprographics
Digital File Management
This department is related to Architect/engineers, but can also apply to any other industry needing electronic document management, scanning, or archival services.
BYLine for optional use: Effective & Efficient Digital Solutions at every level.
Related Pages:
http://www.klmvxco.example/colorgraphics/electronic_file_document_management
http://www.klmvxco.example/colorgraphics/document_scanning_service
http://www.klmvxco.example/services/scanning_and_archiving

Color Graphics
This Department is newly expanded / has expanded services / they are focusing more of their efforts on this department and is a key reason for updated website design.
This Department image/representation should be stellar in the imagery to convey the excellence of the color department the services availble.
One of their newest products/services is dimensional printing – not 3-D, but raised element printing. Essentially a client could pick components on their graphic that that they want to 'bump' out, and additional layers would be put in place to create a popped out, dimensional effect. * Bonus points for creating the color department image that effectively conveys this new service – whether it's showing an abstract image/element that is actually raised off the page/paper/component. Additionally the color dimensional printing can be done on practically any material – glass, vinyl, material etc.... Please let me know if you have any questions on this.
BYLine for optional Use: See How Our Color Stands Out From the Rest
Related pages:
http://www.klmvxco.example/colorgraphics
http://www.klmvxco.example/colorgraphics/color_digital_imaging

Equipment & Supplies
This department provides specific supplies and hardware vs. printing products/services. Our largest client base is architects/engineers, but is not limited to this industry. Typical equipment is large printers, and supplies are typically paper products geared to the large format printing services, for the architect/engineers industry.
Byline for optional Use: In-House Printing & Fulfillment Services
Related pages:
http://www.klmvxco.example/tarvo_ulix_equipment_sales
http://www.klmvxco.example/supplies

Additionally - Possibly have descriptive text sections below these 4 elements, but this is optional.

2.) Department/Division Page design -

This page should pull the home page element to over based on which division is selected.
Have a submenu design incorporated so that users can navigate to all the products and services that will be listed under that division
Contain a plugin design for FAQs – so that depending on which division page they are on, the appropriate FAQ's would display for use to have easy access to.
Contain a plugin design for – Contact Us easy form – short form –
Name
Company
Number
Email
Project Details/Questions: Text box

3.)Content Page design
This page should have main area for content
Area for an image with slideshow of other supporting images
Optional area for video – most (99%) of the pages will not have videos, but in the case we do, would like an area that will display videos effectively.
Optional FAQ plugin display
Contact plugin display

Global Elements:

Static and very visible site features that are in a position so that if user clicks beyond home page will still see these are:
Get a Quote
Place Order
Digital Plan-room
Call Today - 555-384-7290

Other global components:
SM Icons – QN, Chirpa, Workrung
Rotating Testimonial

Navigational Menu:
The KLM Difference
About
Sustainability
Products & Services
Reprograhics
Digital File Management
Color Graphics
Equipment & Supplies
Login
Blog
Contact Us

After the contest – What would be great to have is when a user clicks on one of the departments, it takes that visual element and continues onto it's department page for a smaller but related image - But this may be an after this web design contest.

Additionally will need some other design work on the interior pages, as well, so hoping to find a great designer to complete the other tasks – as well as be the go-to for future endeavors!

Thanks for looking at the project, and I look forward to any questions you may have.
Updates

Looking forward to hearing from interested designers! - If you're curious about my work, you can find my profile at:  https://www.jobrilly.example/users/~07f3b92e61cd5a0b48

Target Market(s)

Please see description

Industry/Entity Type

Electronic

Requirements
Must have
• Please see description

```html
<!DOCTYPE html>
<html lang="en">
<head>
<meta charset="utf-8">
<title>KLM Print &amp; Blueprint – Digital Imaging</title>
<link rel="stylesheet" href="https://fonts.googleapis.com/css2?family=Mulish:ital,wght@0,400;0,600;0,700;1,400&display=swap">
<style>
:root{
  --brand-navy:#2a3590;
  --hero-blue:#0e6aab;
  --arrow-blue:#0d6db5;
  --ink:#111;
  --muted:#8a8a8a;
  --icon-grey:#9a9a9a;
  --rule:#dedede;
  --band-grey:#e6e6e6;
  --footer:#000;
  --white:#fff;
}
*{box-sizing:border-box;margin:0;padding:0}
html,body{width:1200px;height:1126px;overflow:hidden;background:var(--white)}
body{font-family:"Mulish",Arial,sans-serif;color:var(--ink);position:relative}
a{color:inherit;text-decoration:none}

.site-header{position:absolute;left:0;top:0;width:1200px;height:138px;border-bottom:1px solid var(--rule)}
.brand{position:absolute;left:138px;top:40px;display:flex;align-items:center;gap:12px}
.brand-mark{width:46px;height:46px;background:var(--brand-navy)}
.brand-name{font-weight:700;font-size:20px;line-height:24px;color:var(--brand-navy);width:230px}
.utility-nav{position:absolute;right:124px;top:38px;font-size:12.5px;font-weight:600;display:flex}
.utility-nav a{padding:0 7px;border-left:1px solid var(--ink);line-height:13px}
.utility-nav a:first-child{border-left:0}
.utility-nav a:last-child{padding-right:0}
.social{position:absolute;left:909px;top:74px;display:flex;gap:27px}
.social span{width:18px;height:18px;border-radius:50%;background:#8c8c8c}

.main-nav{position:absolute;left:131px;top:138px;height:45px;display:flex;gap:16px;align-items:center;font-size:10.8px;font-weight:700;text-transform:uppercase;letter-spacing:-.25px;white-space:nowrap}

.hero{position:absolute;left:0;top:183px;width:1200px;height:501px}
.hero svg.hero-bg{position:absolute;inset:0}
.hero-copy{position:absolute;left:134px;top:80px;color:var(--white);width:470px}
.hero-title{font-weight:400;font-size:42px;line-height:44px;letter-spacing:0}
.hero-text{margin-top:22px;font-size:14.5px;line-height:22px;width:455px}
.order-button{position:absolute;left:1px;top:172px;width:218px;height:56px;border-radius:3px;background:linear-gradient(#fdfdfd,#d9d9d9);box-shadow:0 2px 3px rgba(0,0,0,.35);overflow:hidden}
.order-button .chevron{position:absolute;left:0;top:12px;width:31px;height:31px;background:var(--brand-navy)}
.order-button .label{position:absolute;left:38px;top:9px;width:156px;font-size:15px;font-weight:700;color:#555;line-height:19px;text-align:center;white-space:nowrap;letter-spacing:-.1px}
.order-button .ribbon{position:absolute;right:0;bottom:0}
.slide-prev,.slide-next{position:absolute;top:198px;width:57px;height:58px;display:flex;align-items:center;justify-content:center}
.slide-prev{left:21px;border:1px solid var(--white)}
.slide-next{left:1124px;background:var(--arrow-blue)}

.band{position:absolute;left:0;top:684px;width:1200px;height:70px;background:var(--band-grey)}
.divisions{position:absolute;left:110px;top:560px;width:980px;height:181px;background:var(--white);display:flex}
.division{flex:none;height:181px;border-left:1px solid var(--rule);text-align:center;position:relative}
.division:first-child{border-left:0}
.division svg{position:absolute;top:22px;left:50%;transform:translateX(-50%)}
.division-name{position:absolute;left:0;right:0;top:133px;font-size:15.5px;color:var(--brand-navy);letter-spacing:-.1px}

.info{position:absolute;top:754px;left:0;width:1200px;height:318px}
.col-title{position:absolute;top:30px;font-size:14px;font-weight:700;text-transform:uppercase;letter-spacing:-.1px}
.photo{position:absolute;border:1px solid #ccc}
.body-text{position:absolute;font-size:12.5px;line-height:19px;color:var(--muted);letter-spacing:-.2px}
.read-more{position:absolute;font-size:12.5px;font-style:italic;color:#333}
.news-item{position:absolute;left:477px;width:275px;font-size:12.2px;line-height:19px;color:var(--muted);letter-spacing:-.2px}
.news-item .meta{color:var(--brand-navy)}
.news-item .meta i{font-style:italic}
.news-rule{position:absolute;left:477px;top:160px;width:271px;border-top:1px solid var(--rule)}
.testi-arrows{position:absolute;left:1048px;top:32px}
.quote{position:absolute;left:902px;width:174px;font-size:11.5px;line-height:18px;color:var(--muted);letter-spacing:-.15px}
.quote-name{position:absolute;left:902px;font-size:11px;font-weight:700;color:var(--brand-navy);text-transform:uppercase}

.site-footer{position:absolute;left:0;top:1072px;width:1200px;height:54px;background:var(--footer);color:var(--white);font-size:12px}
.site-footer .copy{position:absolute;left:130px;top:20px}
.site-footer .contact{position:absolute;right:127px;top:20px}
</style>
</head>
<body>

<header class="site-header">
  <a class="brand" href="#"><span class="brand-mark"></span><span class="brand-name">KLM Print &amp; Blueprint</span></a>
  <nav class="utility-nav"><a href="#">LOGIN</a><a href="#">BLOG</a><a href="#">CONTACT US</a></nav>
  <div class="social"><span></span><span></span><span></span><span></span></div>
</header>

<nav class="main-nav">
  <a href="#">The KLM Difference</a><a href="#">About</a><a href="#">Sustainability</a><a href="#">Products &amp; Services</a><a href="#">Reprograhics</a><a href="#">Digital File Management</a><a href="#">Color Graphics</a><a href="#">Equipment &amp; Supplies</a>
</nav>

<section class="hero">
  <svg class="hero-bg" width="1200" height="501" viewBox="0 0 1200 501">
    <defs><linearGradient id="plans" x1="0" y1="0" x2="1" y2="1"><stop offset="0" stop-color="#f4f5f6"/><stop offset="1" stop-color="#d6d8da"/></linearGradient></defs>
    <rect role="img" aria-label="Rolled blueprints, technical drawings and a pencil" x="0" y="0" width="1200" height="501" fill="url(#plans)"/>
    <polygon points="0,0 612,0 690,377 690,501 0,501" fill="var(--hero-blue)"/>
  </svg>
  <div class="hero-copy">
    <h1 class="hero-title">Services for Architects Engineers &amp; Builders</h1>
    <p class="hero-text">Lorem Ipsum is simply dummy text of the printing and typesetting industry. Lorem Ipsum has been the industry's standard dummy text.</p>
    <a class="order-button" href="#">
      <span class="chevron"><svg width="31" height="31" viewBox="0 0 31 31"><path d="M10 9l5.5 5 5.5-5M10 15l5.5 5 5.5-5" fill="none" stroke="#fff" stroke-width="2.5"/></svg></span>
      <span class="label">PLACE AN<br>ORDER HERE FREE</span>
      <svg class="ribbon" width="30" height="30" viewBox="0 0 30 30"><polygon points="30,4 30,18 18,30 4,30" fill="var(--brand-navy)"/><text x="21" y="25" font-size="6" fill="#fff" font-family="Mulish,sans-serif" transform="rotate(-45 21 23)">NEW</text></svg>
    </a>
  </div>
  <a class="slide-prev" href="#" aria-label="Previous slide"><svg width="14" height="16" viewBox="0 0 14 16"><path d="M10 2L4 8l6 6" fill="none" stroke="#fff" stroke-width="3"/></svg></a>
  <a class="slide-next" href="#" aria-label="Next slide"><svg width="14" height="16" viewBox="0 0 14 16"><path d="M4 2l6 6-6 6" fill="none" stroke="#fff" stroke-width="3"/></svg></a>
</section>

<div class="band"></div>

<section class="divisions">
  <a class="division" href="#" style="width:245px">
    <svg width="86" height="84" viewBox="0 0 86 84" fill="var(--icon-grey)"><polygon points="38,0 24,16 32,16 32,34 44,34 44,16 52,16"/><rect x="0" y="38" width="52" height="22"/><circle cx="60" cy="56" r="24" fill="#fff"/><circle cx="60" cy="56" r="21" fill="none" stroke="var(--icon-grey)" stroke-width="5"/><path d="M49 56l8 8 14-15" fill="none" stroke="var(--icon-grey)" stroke-width="5"/></svg>
    <span class="division-name">Order Form &amp; Upload</span></a>
  <a class="division" href="#" style="width:242px">
    <svg width="80" height="80" viewBox="0 0 80 80" fill="none" stroke="var(--icon-grey)" stroke-width="3.5"><circle cx="40" cy="40" r="37"/><ellipse cx="40" cy="40" rx="16" ry="37"/><path d="M40 3v74M3 40h74M8 22h64M8 58h64"/></svg>
    <span class="division-name">PlanVault Dfs Digital Platform</span></a>
  <a class="division" href="#" style="width:242px">
    <svg width="70" height="80" viewBox="0 0 70 80" fill="var(--icon-grey)"><circle cx="35" cy="18" r="18"/><path d="M0 80V54q0-14 14-14h42q14 0 14 14v26z"/><path d="M30 40h10l-5 26z" fill="#fff"/><rect x="44" y="62" width="14" height="3" fill="#fff"/></svg>
    <span class="division-name">Online Account Information</span></a>
  <a class="division" href="#" style="width:251px">
    <svg width="98" height="86" viewBox="0 0 98 86" fill="none" stroke="var(--icon-grey)" stroke-width="5"><polygon points="49,4 94,26 49,48 4,26"/><path d="M4 42l45 22 45-22M4 58l45 22 45-22"/><path d="M18 26l31-14 31 14-31 10z" fill="var(--icon-grey)" stroke="none"/></svg>
    <span class="division-name">Dimensional Printing</span></a>
</section>

<section class="info">
  <h2 class="col-title" style="left:132px">About Us</h2>
  <div class="photo" role="img" aria-label="City riverfront with bridge" style="left:130px;top:74px;width:109px;height:88px;background:linear-gradient(#b9c9d6,#7d8c7a 55%,#5f7385)"></div>
  <p class="body-text" style="left:248px;top:70px;width:204px">Lorem Ipsum is simply dummy text of the printing and typesetting industry. Lorem Ipsum has been the industry's standard dummy text ever since the 1500s.</p>
  <p class="body-text" style="left:131px;top:165px;width:320px">Lorem Ipsum is simply dummy text of the printing and typesetting industry. Lorem Ipsum has been the industry's standard dummy text ever since the 1500s Ipsum has been the industry's standard dummy text ever since the 1500s.</p>
  <a class="read-more" href="#" style="left:131px;top:264px">Read More</a>

  <h2 class="col-title" style="left:479px">News &amp; Events</h2>
  <div class="news-item" style="top:68px"><span>Harlow Ridge Coastal Sauvignon</span> <span class="meta">Blanc – <i>posted on March 13, 2013 20:15</i></span><br>Harlow Ridge Coastal Sauvignon blended</div>
  <a class="read-more" href="#" style="left:477px;top:138px">Read More</a>
  <div class="news-rule"></div>
  <div class="news-item" style="top:177px"><span>Harlow Ridge Coastal Sauvignon</span> <span class="meta">Blanc – <i>posted on March 13, 2013 20:15</i></span><br>Media release; summer has never tasted better than with Harlow Ridge's 2012 Blanc</div>
  <a class="read-more" href="#" style="left:478px;top:264px">Read More</a>

  <h2 class="col-title" style="left:780px">Testimonials</h2>
  <svg class="testi-arrows" width="22" height="14" viewBox="0 0 22 14"><path d="M7 2L2 7l5 5M15 2l5 5-5 5" fill="none" stroke="#111" stroke-width="2"/></svg>
  <div class="photo" role="img" aria-label="Portrait of a smiling client" style="left:783px;top:74px;width:107px;height:88px;background:linear-gradient(135deg,#dfe7ee,#b8a597)"></div>
  <p class="quote" style="top:71px">“Lorem Ipsum is simply dummy text of the printing and typesetting industry. Lorem Ipsum has been the industrys”</p>
  <span class="quote-name" style="top:148px">Dorian Welsh</span>
  <div class="photo" role="img" aria-label="Portrait of a client in a suit" style="left:783px;top:188px;width:107px;height:88px;background:linear-gradient(135deg,#f2f2f2,#7a6a5e)"></div>
  <p class="quote" style="top:187px">“Lorem Ipsum is simply dummy text of the printing and typesetting industry. Lorem Ipsum has been the industry's”</p>
  <span class="quote-name" style="top:264px">Roland Thayer</span>
</section>

<footer class="site-footer">
  <span class="copy">Copyright 2013 Kestrel Lane Print &amp; Blueprint Inc.</span>
  <span class="contact">Questions/Comments: email us at info@klmvxco.example</span>
</footer>

</body>
</html>
```